Website Design for Employee Moral and Happiness Company

Looking for a clean website design that explains our features in a step by step manner so our visitors know exactly what our site does before logging in.

The site is called "Velrato". See logo design and video for a sample of style and an overview of what we do.

Target Market(s)

Business owners that are looking to retain employees.

Number of Pages Required

1 page

```html
<!DOCTYPE html>
<html lang="en">
<head>
<meta charset="utf-8">
<title>Velrato — Employee Morale &amp; Happiness</title>
<link href="https://fonts.googleapis.com/css2?family=Poppins:ital,wght@0,400;0,500;0,600;0,700;1,400&display=swap" rel="stylesheet">
<style>
:root{
  --orange:#f4540c;
  --ink:#1d1d1f;
  --text:#444;
  --muted:#666;
  --black:#000;
  --soft:#f2f4f7;
  --line:#555;
  --footer:#1f1d1c;
  --white:#fff;
}
*{box-sizing:border-box;margin:0;padding:0}
html,body{width:1200px;height:4739px;overflow:hidden}
body{font-family:"Poppins",sans-serif;color:var(--text);background:var(--white);position:relative}
.abs{position:absolute}
a{color:inherit;text-decoration:none}

/* header */
.topbar{top:0;left:0;width:1200px;height:83px;background:var(--white)}
.brand{left:110px;top:12px;font:700 42px "Poppins",sans-serif;color:var(--ink);letter-spacing:1px}
.contact-chip{display:flex;align-items:center;gap:16px;top:15px}
.chip-icon{width:50px;height:50px;border-radius:50%;background:var(--orange);display:flex;align-items:center;justify-content:center}
.chip-label{font-size:13px;color:#4a5a8a;line-height:1.2}
.chip-value{font-size:17px;color:var(--ink);line-height:1.4}
.navbar{top:83px;left:0;width:1200px;height:51px;background:var(--black)}
.nav-item{top:0;height:51px;line-height:51px;font-size:15px;color:var(--white)}
.nav-item.active{background:var(--orange);padding:0 16px}
.login{right:110px;top:0;height:51px;display:flex;align-items:center;gap:7px;color:var(--white);font-size:16px}

/* hero */
.hero-photo{top:134px;left:0;width:1200px;height:661px;background:linear-gradient(180deg,#43566b 0%,#3a4a5c 55%,#2d3440 100%)}
.hero-title{top:172px;left:0;width:1200px;text-align:center;font:600 66px "Poppins",sans-serif;color:var(--white)}
.hero-text{top:258px;left:230px;width:740px;text-align:center;font-size:14px;line-height:32px;color:var(--white)}
.btn{background:var(--orange);color:var(--white);font-weight:600;font-size:16px;border-radius:30px;display:flex;align-items:center;justify-content:center;box-shadow:0 4px 10px rgba(244,84,12,.3)}
.hero-btn{left:500px;top:337px;width:200px;height:50px}

/* who we are */
.pattern{left:0;top:795px;width:366px;height:368px;background:#f1f1f1}
.frame{border:1.5px solid var(--orange)}
.who-photo{left:112px;top:939px;width:446px;height:438px;background:linear-gradient(135deg,#8a7b6a,#cfc6b9 50%,#5a4f45)}
.section-title{font:600 40px "Poppins",sans-serif;color:var(--ink)}
.who-title{left:626px;top:934px;color:var(--orange)}
.bar{height:4px;background:var(--ink)}
.bullet{left:620px;width:440px;font-size:13px;line-height:27.6px;color:var(--text);padding-left:20px}
.bullet::before{content:"";position:absolute;left:0;top:9px;width:10px;height:10px;border-radius:50%;background:var(--orange);box-shadow:inset 0 0 0 2px var(--orange),inset 0 0 0 3px var(--white)}
.who-btn{left:618px;top:1307px;width:201px;height:51px}

/* features */
.features{top:1500px;left:0;width:1200px;height:594px;background:var(--soft)}
.center-title{left:0;width:1200px;text-align:center}
.orange-bar{height:4px;background:var(--orange)}
.feature-card{left:434px;top:1682px;width:332px;height:324px;background:var(--white);border:2px solid var(--orange);border-radius:10px;box-shadow:0 6px 18px rgba(0,0,0,.1)}
.feature-icon{width:114px;height:103px;background:var(--white);border-radius:6px;box-shadow:0 3px 12px rgba(0,0,0,.15);display:flex;align-items:center;justify-content:center}
.feature-title{width:310px;text-align:center;font:500 15px "Poppins",sans-serif;color:var(--ink)}
.feature-text{width:310px;text-align:center;font-size:12.5px;line-height:25px;color:var(--muted)}
.link{color:var(--orange);font-weight:500;font-size:14px;text-decoration:underline}

/* video */
.video{top:2094px;left:0;width:1200px;height:509px;background:linear-gradient(135deg,#c9c3b9 0%,#2f7f8c 45%,#1c2b3a 70%,#c9c3b9 100%)}
.play{left:560px;top:2308px;width:78px;height:78px;border:2px solid rgba(255,255,255,.8);border-radius:50%;display:flex;align-items:center;justify-content:center}

/* articles */
.article-img{top:2803px;width:313px;height:263px;border-radius:14px;box-shadow:0 4px 10px rgba(0,0,0,.15)}
.article-date{font-size:12.5px;color:var(--muted);display:flex;align-items:center;gap:8px}
.article-title{font:500 15px "Poppins",sans-serif;color:var(--ink)}
.article-text{width:300px;font-size:12.5px;line-height:26px;color:var(--muted)}
.dots{top:3330px;left:558px;display:flex;gap:3px}
.dot{width:14px;height:14px;border-radius:50%;background:#222}
.dot.open{background:var(--white);border:1.5px solid #222}

/* reviews */
.reviews{top:3447px;left:0;width:731px;height:250px;background:var(--orange)}
.reviews-img{top:3447px;left:731px;width:469px;height:250px;background:linear-gradient(90deg,#dfe5ea,#a9b6bf 55%,#7d6b5a)}
.reviews-title{left:111px;top:3477px;font:600 34px "Poppins",sans-serif;color:var(--white)}
.reviews-text{left:110px;top:3545px;width:580px;font-style:italic;font-size:13px;line-height:26px;color:var(--white)}
.reviews-name{left:111px;top:3632px;font-size:17px;font-weight:500;color:var(--white)}

/* contact */
.contact-text{top:3866px;left:270px;width:660px;text-align:center;font-size:13px;line-height:26px;color:var(--muted)}
.field{font-size:14px;color:var(--muted);border-bottom:2px solid var(--line);padding-bottom:8px}
.submit{left:471px;top:4252px;width:258px;height:51px}

/* footer */
.footer{top:4395px;left:0;width:1200px;height:344px;background:linear-gradient(90deg,#1c1b1a,#2a2725 60%,#1c1b1a);color:#ddd}
.footer-brand{left:110px;top:4448px;font:700 36px "Poppins",sans-serif;color:var(--white);letter-spacing:1px}
.footer-text{left:110px;top:4498px;width:370px;font-size:12px;line-height:25.5px;color:#ddd}
.footer-head{font:500 17px "Poppins",sans-serif;color:var(--white)}
.footer-link{font-size:13px;color:#ddd}
.footer-link::before{content:"» ";}
.social{width:31px;height:31px;background:var(--orange)}
.copyright{top:4700px;left:0;width:1200px;text-align:center;font-size:13px;color:#eee}
.divider{top:4684px;left:0;width:1200px;height:1px;background:rgba(255,255,255,.12)}
</style>
</head>
<body>

<header class="abs topbar">
  <div class="abs brand">Velrato</div>
  <div class="abs contact-chip" style="left:586px">
    <span class="chip-icon"><svg width="20" height="20" viewBox="0 0 24 24"><path fill="#fff" d="M6.6 10.8a15 15 0 0 0 6.6 6.6l2.2-2.2a1 1 0 0 1 1-.25 11.4 11.4 0 0 0 3.6.57 1 1 0 0 1 1 1V20a1 1 0 0 1-1 1A17 17 0 0 1 3 4a1 1 0 0 1 1-1h3.5a1 1 0 0 1 1 1c0 1.25.2 2.45.57 3.57a1 1 0 0 1-.25 1z"/></svg></span>
    <div><div class="chip-label">Call Now</div><div class="chip-value">+1 (888) 888 8888</div></div>
  </div>
  <div class="abs contact-chip" style="left:834px">
    <span class="chip-icon"><svg width="20" height="16" viewBox="0 0 20 16"><rect x="0" y="0" width="20" height="16" rx="2" fill="#fff"/><path d="M1 2l9 7 9-7" stroke="#f4540c" stroke-width="2" fill="none"/></svg></span>
    <div><div class="chip-label">Email Now</div><div class="chip-value">Contact@Velrato.com</div></div>
  </div>
</header>

<nav class="abs navbar">
  <a class="abs nav-item active" style="left:112px">Home</a>
  <a class="abs nav-item" style="left:215px">About &nbsp;Us</a>
  <a class="abs nav-item" style="left:330px">What we do</a>
  <a class="abs nav-item" style="left:464px">Our Video</a>
  <a class="abs nav-item" style="left:582px">Reviews</a>
  <a class="abs nav-item" style="left:683px">Blog</a>
  <a class="abs nav-item" style="left:758px">Contact</a>
  <a class="abs login"><svg width="13" height="14" viewBox="0 0 13 14"><circle cx="6.5" cy="3.5" r="3.3" fill="#fff"/><path d="M0 14c0-4 2.8-6 6.5-6S13 10 13 14z" fill="#fff"/></svg>Login</a>
</nav>

<section>
  <div class="abs hero-photo" role="img" aria-label="Photo of five smiling coworkers seated against a blue wall with laptops and tablets"></div>
  <h1 class="abs hero-title">Velrato</h1>
  <p class="abs hero-text">Lorem ipsum dolor sit amet, consectetur adipiscing elit, eiusmod tempor incididunt ut labore et dolore magna aliqua. &nbsp;Lorem ipsum dolor sit amet, consectetur adipiscing elit, eiusmod</p>
  <a class="abs btn hero-btn">Get Started</a>
</section>

<section>
  <div class="abs pattern" role="img" aria-label="Light diagonal line texture"></div>
  <div class="abs frame" style="left:212px;top:906px;width:370px;height:364px"></div>
  <div class="abs frame" style="left:68px;top:1207px;width:214px;height:210px;background:var(--white)"></div>
  <div class="abs who-photo" role="img" aria-label="Photo of a smiling woman in a trench coat holding a laptop"></div>
  <h2 class="abs section-title who-title">Who We Are</h2>
  <div class="abs bar" style="left:626px;top:1001px;width:107px"></div>
  <p class="abs bullet" style="top:1031px">Lorem ipsum dolor sit amet, consectetur adipiscing elit, sed do eiusmod tempor incididunt ut labore et dolore magna aliqua. Ut enim ad minim veniam, quis nostrud exercitation ullamco laboris nisi ut aliquip ex ea commodo consequat. Duis aute irure dolor in reprehenderit</p>
  <p class="abs bullet" style="top:1197px">Lorem ipsum dolor sit amet, consectetur adipiscing elit, sed do eiusmod tempor incididunt ut labore et dolore magna aliqua. Ut consequat. Duis aute irure dolor in reprehenderit</p>
  <a class="abs btn who-btn">Read More</a>
</section>

<section class="abs features">
  <h2 class="abs section-title center-title" style="top:70px">Our Features</h2>
  <div class="abs orange-bar" style="left:576px;top:134px;width:77px"></div>
</section>
<div class="abs feature-card"></div>

<div class="abs feature-icon" style="left:208px;top:1717px">
  <svg width="70" height="70" viewBox="0 0 70 70" fill="none" stroke="#f4540c" stroke-width="2"><rect x="8" y="6" width="40" height="52" rx="2"/><path d="M15 16h20M15 24h26M15 32h14"/><rect x="28" y="38" width="34" height="24" rx="2"/><path d="M38 38v-5h14v5M28 48h34"/></svg>
</div>
<div class="abs feature-icon" style="left:543px;top:1717px;box-shadow:none">
  <svg width="80" height="50" viewBox="0 0 80 50" fill="none" stroke="#f4540c" stroke-width="2"><path d="M2 10l14-4 8 26-14 4zM78 10l-14-4-8 26 14 4z"/><path d="M24 12l12-4 8 4 12-4 6 22-16 14c-3 2-6 0-5-2-3 1-6-1-5-3-3 1-6-1-5-3-3 0-5-2-4-4l4-4"/><path d="M44 12l-10 8c-2 2 0 5 3 4l9-5"/></svg>
</div>
<div class="abs feature-icon" style="left:878px;top:1717px">
  <svg width="70" height="70" viewBox="0 0 70 70" fill="none" stroke="#f4540c" stroke-width="2"><rect x="6" y="6" width="14" height="14"/><path d="M9 13l3 3 6-6"/><rect x="50" y="50" width="14" height="14"/><path d="M53 57l3 3 6-6"/><rect x="6" y="50" width="14" height="14"/><path d="M9 53l8 8M17 53l-8 8"/><circle cx="35" cy="35" r="12"/><circle cx="35" cy="35" r="6"/><circle cx="35" cy="35" r="1.5" fill="#f4540c"/><path d="M26 10a26 26 0 0 1 30 10M60 30v10M13 30v12"/></svg>
</div>

<h3 class="abs feature-title" style="left:110px;top:1840px">Lorem ipsum dolor sit</h3>
<p class="abs feature-text" style="left:110px;top:1868px">Sed do eiusmod tempor incididunt ut labore et dolore magna aliqua. Ut enim veniam, quis nostrud exercitation ullamco</p>
<h3 class="abs feature-title" style="left:445px;top:1840px">Lorem ipsum dolor sit</h3>
<p class="abs feature-text" style="left:445px;top:1868px">Sed do eiusmod tempor incididunt ut labore et dolore magna aliqua. Ut enim veniam, quis nostrud exercitation ullamco</p>
<a class="abs link" style="left:558px;top:1964px">Read More</a>
<h3 class="abs feature-title" style="left:780px;top:1840px">Lorem ipsum dolor sit</h3>
<p class="abs feature-text" style="left:780px;top:1868px">Sed do eiusmod tempor incididunt ut labore et dolore magna aliqua. Ut enim veniam, quis nostrud exercitation ullamco</p>

<section>
  <div class="abs video" role="img" aria-label="Illustration of a man working at a laptop at his desk, video cover"></div>
  <div class="abs play"><svg width="22" height="24" viewBox="0 0 22 24"><path d="M3 2l17 10-17 10z" fill="none" stroke="#fff" stroke-width="2"/></svg></div>
</section>

<section>
  <h2 class="abs section-title center-title" style="top:2694px">Latest Article</h2>

  <div class="abs article-img" style="left:110px;background:linear-gradient(135deg,#8ca3b8,#e8eef2 55%,#6b7f92)" role="img" aria-label="Photo of a smiling man in glasses at his desk"></div>
  <div class="abs article-img" style="left:442px;background:linear-gradient(135deg,#dfe3e6,#8d9aa3 55%,#4a4f55)" role="img" aria-label="Photo of a team meeting around a table with laptops"></div>
  <div class="abs article-img" style="left:771px;background:linear-gradient(135deg,#b9c7cf,#e3e7ea 50%,#6e7a7f)" role="img" aria-label="Photo of colleagues collaborating around a laptop"></div>

  <div class="abs article-date" style="left:112px;top:3090px"><svg width="13" height="13" viewBox="0 0 13 13"><rect x="0.5" y="2" width="12" height="10.5" fill="#f4540c"/><path d="M3 0v3M10 0v3" stroke="#f4540c" stroke-width="1.5"/></svg>Jan-31-2022</div>
  <h3 class="abs article-title" style="left:110px;top:3123px">Lorem ipsum dolor sit amet</h3>
  <p class="abs article-text" style="left:110px;top:3156px">Sed do eiusmod tempor incididunt ut labore et dolore magna aliqua. Ut enim ad minim veniam, quis nostrud exercitation</p>
  <a class="abs link" style="left:110px;top:3247px">Read More</a>

  <div class="abs article-date" style="left:442px;top:3090px"><svg width="13" height="13" viewBox="0 0 13 13"><rect x="0.5" y="2" width="12" height="10.5" fill="#f4540c"/><path d="M3 0v3M10 0v3" stroke="#f4540c" stroke-width="1.5"/></svg>Jan-31-2022</div>
  <h3 class="abs article-title" style="left:442px;top:3123px">Lorem ipsum dolor sit amet</h3>
  <p class="abs article-text" style="left:442px;top:3156px">Sed do eiusmod tempor incididunt ut labore et dolore magna aliqua. Ut enim ad minim veniam, quis nostrud exercitation</p>
  <a class="abs link" style="left:442px;top:3247px">Read More</a>

  <div class="abs article-date" style="left:772px;top:3090px"><svg width="13" height="13" viewBox="0 0 13 13"><rect x="0.5" y="2" width="12" height="10.5" fill="#f4540c"/><path d="M3 0v3M10 0v3" stroke="#f4540c" stroke-width="1.5"/></svg>Jan-31-2022</div>
  <h3 class="abs article-title" style="left:772px;top:3123px">Lorem ipsum dolor sit amet</h3>
  <p class="abs article-text" style="left:772px;top:3156px">Sed do eiusmod tempor incididunt ut labore et dolore magna aliqua. Ut enim ad minim veniam, quis nostrud exercitation</p>
  <a class="abs link" style="left:772px;top:3247px">Read More</a>

  <div class="abs dots"><span class="dot"></span><span class="dot"></span><span class="dot open"></span><span class="dot"></span><span class="dot"></span></div>
</section>

<section>
  <div class="abs reviews"></div>
  <div class="abs reviews-img" role="img" aria-label="Photo of a smiling woman holding a tablet in a bright office"></div>
  <h2 class="abs reviews-title">Client Reviews</h2>
  <p class="abs reviews-text">Lorem ipsum dolor sit amet, consectetur adipiscing elit, sed do eiusmod tempor incididunt ut labore et dolore magna aliqua. Ut enim ad minim veniam, quis nostrud exercitation ullamco laboris nisi ut aliquip ex ea commodo</p>
  <p class="abs reviews-name">John Doe</p>
</section>

<section>
  <h2 class="abs section-title center-title" style="top:3780px">Contact Us</h2>
  <p class="abs contact-text">Lorem ipsum dolor sit amet, consectetur adipiscing elit, sed do eiusmod tempor incididunt ut labore et dolore magna aliqua. Ut enim ad</p>
  <div class="abs field" style="left:228px;top:3960px;width:350px">First Name</div>
  <div class="abs field" style="left:622px;top:3960px;width:350px">Last Name</div>
  <div class="abs field" style="left:228px;top:4030px;width:350px">Email Address</div>
  <div class="abs field" style="left:622px;top:4030px;width:350px">Phone Number</div>
  <div class="abs field" style="left:228px;top:4098px;width:740px;height:100px">Message</div>
  <a class="abs btn submit">Submit Now</a>
</section>

<footer class="abs footer" role="img" aria-label="Dark office photo backdrop"></footer>
<div class="abs footer-brand">Velrato</div>
<p class="abs footer-text">Lorem ipsum dolor sit amet, consectetur adipiscing elit, sed do eiusmod tempor incididunt ut labore et dolore magna aliqua. Ut enim ad minim veniam, quis nostrud exercitation ullamco laboris nisi ut aliquip ex ea commodo consequat. Duis aute irure dolor in reprehenderit</p>

<h4 class="abs footer-head" style="left:537px;top:4456px">Quick Links</h4>
<a class="abs footer-link" style="left:535px;top:4503px">Home</a>
<a class="abs footer-link" style="left:535px;top:4532px">About us</a>
<a class="abs footer-link" style="left:535px;top:4561px">What we do</a>
<a class="abs footer-link" style="left:535px;top:4591px">Blog</a>
<a class="abs footer-link" style="left:535px;top:4620px">Our Videos</a>
<a class="abs footer-link" style="left:721px;top:4503px">Reviews</a>
<a class="abs footer-link" style="left:721px;top:4532px">FAQ's</a>
<a class="abs footer-link" style="left:721px;top:4561px">Contact</a>

<h4 class="abs footer-head" style="left:894px;top:4456px">Contact Us</h4>
<div class="abs" style="left:898px;top:4500px;display:flex;align-items:center;gap:6px;color:#fff;font-size:15px;font-weight:500">
  <span style="width:30px;height:30px;border:1px solid #aaa;border-radius:50%;display:flex;align-items:center;justify-content:center"><svg width="14" height="14" viewBox="0 0 24 24"><path fill="#ddd" d="M6.6 10.8a15 15 0 0 0 6.6 6.6l2.2-2.2a1 1 0 0 1 1-.25 11.4 11.4 0 0 0 3.6.57 1 1 0 0 1 1 1V20a1 1 0 0 1-1 1A17 17 0 0 1 3 4a1 1 0 0 1 1-1h3.5a1 1 0 0 1 1 1c0 1.25.2 2.45.57 3.57a1 1 0 0 1-.25 1z"/></svg></span>+1 888 888 8888
</div>
<div class="abs social" style="left:907px;top:4562px"></div>
<div class="abs social" style="left:953px;top:4562px"></div>
<div class="abs social" style="left:999px;top:4562px"></div>
<div class="abs social" style="left:1046px;top:4562px"></div>

<div class="abs divider"></div>
<p class="abs copyright">© 2022 All Rights Reserved</p>

</body>
</html>
```